www.lanternmerow.net

Hi,
UPDATE: Logo attached
TAG LINE NEW: OBITUARIES * CONDOLENCE NOTES
MULTIMEDIA MEMORIAL
Please refer to our existing site for more explanation of who we are?
We are a global data collecting portal site managing the Jewish funeral industry where users:
a) family and freinds in grief or "ancestry" searching persons
b) chevra kadisha's (funeral parlor)
c) current and historic cemetaries
d) Jewish Media Partners
arrive and choose a function (category):
in order to:
- upload a basic listing (FREE)
- upload/upgrade a multimedia listing (PAID)
- or search for a listing
of a deceased person (potentially millions of entries)
The functions (or categories) are accessed after the user:
Chooses their global location of search by
"Choose your Location" ie: Australia/NZ (which country?)
and allows the USER to choose a category function such as:
GROUP A (Local Info) GROUP B (Soul Search)
Chevra Kadisha Funerals (within 7 days)
Cemetaries Recently Deceased (up to 12mth)
Stonemasons Soul Search (after 1 year)
Jewish Media Partners
GROUP C (Jewish Death & Mourning Customs)
The way of Jewish burial
3000 y/old customs
When will Moshiach Come ?
Will I see my loved one again?
AIM:
To utilize existing logo and side menus (Member, Main & Resources) to create a user freindly and simpler friendly landing page, warmer and more softer for viewers.
To create logo buttons for the service catogories:
A, B & C and separate sub catagories
The MAIN AIM is to offer users opportunity to upload (LOG-IN required)
a) NEW basic FREE listing
b) NEW Multi-media PAID listing
SUMMARY:
1) User arrives at landing paid and sees global map, where he/she must choose the location in order to localize his data search
At this point, he/she can see what the site offers by the side MAIN, menu and icon function/catagories
(ie: Soul Search, New Basic Listing, Multimedia Listing)
2) After arriving at location (ie: Australia/NZ), the user then chooses the sub-function icon:
A- Local Funeral Service Info (Chevra Kadisha, Cemetary etc)
B- Soul Search (Funeral,Recently Deceased, Soul Search)
C- Jewish Death & Mourning Cutoms
Updates
Hi
Reason: Because of the holidays, we are happy to extend the deadline....
happy times
Target Market(s)
Family persons (Guest Member) & Industry (Members)
Industry/Entity Type
Industry
Requirements
Must have
- Style : Simple, Neat & Easy to Navigate
Icons: for each catagory/function
Colors; natural
-
Ability to bring inspiration, hope, light and healing to a difficult subject matter. (site look)
-
Education a profoundly deep 3000 y/old historically rich and mystic tradition to a wide audience
-
Allow children to access and upload data about grandparents etc
-
To promote on landing page the Invitation of local Chevra Kadisha's (funeral parlors), who have no web exposure, to get involved and LOG-IN and upload basic or multimedia listings.
(ie: please Register your local Chevra Kadisha here)
-
To promote on the landing page sample listings (Recently Deceased), to show look/feel of listings

```html
<!DOCTYPE html>
<html lang="en">
<head>
<meta charset="utf-8">
<title>Lanternmerow.net</title>
<link href="https://fonts.googleapis.com/css2?family=Arimo:wght@400;700&family=EB+Garamond:wght@400;500&display=swap" rel="stylesheet">
<style>
:root{
  --orange:#e37b1c;
  --orange-light:#f5a030;
  --brown:#6b3410;
  --blue:#2f8fe6;
  --blue-light:#5fb0f5;
  --ink:#222;
  --grey-text:#555;
  --band:#e6e6e6;
  --panel:#e2e2e2;
  --line:#c9c9c9;
  --white:#fff;
  --map:#3a9ff0;
}
*{box-sizing:border-box;margin:0;padding:0}
html,body{width:750px;height:1200px;overflow:hidden;background:var(--white)}
body{position:relative;font-family:"Arimo",Arial,sans-serif;color:var(--ink);font-size:9px}
.abs{position:absolute}
.serif{font-family:"EB Garamond",Georgia,serif}

.region-bar{left:195px;top:0;width:555px;height:26px;background:var(--brown);clip-path:polygon(0 0,100% 0,100% 100%,28px 100%)}
.region-bar ul{list-style:none;display:flex;position:absolute;left:30px;top:7px;font-size:10px}
.region-bar li{color:var(--orange-light);padding:0 7px;border-left:1px solid #8d4c20}
.region-bar li:first-child{color:var(--white);border-left:none}

.brand{left:30px;top:38px;display:flex;align-items:center;gap:6px}
.brand-dot{width:14px;height:14px;border-radius:50%;background:var(--orange)}
.brand-name{font-family:"EB Garamond",Georgia,serif;font-size:19px;color:var(--ink)}

.search{left:552px;top:61px;width:141px;height:19px;border-radius:10px;background:#ececec;font-size:8px;color:#aaa;padding:5px 8px}
.search svg{position:absolute;right:5px;top:2px}

.main-nav{left:0;width:750px;height:28px;background:linear-gradient(#fafafa,#e2e2e2)}
.main-nav ul{list-style:none;display:flex;position:absolute;left:97px;top:0;height:28px;align-items:center;font-family:"EB Garamond",Georgia,serif;font-size:14px;color:#555}
.main-nav li{padding:0 11px;line-height:28px}
.main-nav li.active{background:#cfcfcf;border-radius:3px 3px 0 0}

.hero{left:25px;top:127px;width:700px;height:228px;border-radius:6px 6px 0 0;background:radial-gradient(ellipse at 45% 45%,#d9a45a,#b7772e 35%,#efe7dc 75%)}
.hero-caption{left:23px;top:355px;width:702px;height:31px;background:var(--white);box-shadow:0 3px 5px rgba(0,0,0,.25);text-align:center;font-family:"EB Garamond",Georgia,serif;font-size:16px;letter-spacing:.5px;line-height:31px;color:#333}
.hero-arrow{top:243px;width:28px;height:28px;background:var(--orange);border-radius:3px}
.hero-arrow svg{position:absolute;left:9px;top:8px}

.page-tab{left:0;top:398px;width:106px;height:33px;background:var(--white);border:1px solid #ccc;box-shadow:2px 2px 4px rgba(0,0,0,.2);font-family:"EB Garamond",Georgia,serif;font-size:17px;color:var(--orange);padding:5px 30px}

.content{left:23px;top:437px;width:492px;font-size:8.6px;line-height:17px}
.content h2{font-family:"EB Garamond",Georgia,serif;font-weight:400;font-size:17px;line-height:20px;margin-bottom:2px}
.content .byline{color:var(--orange);font-weight:700;font-size:9.5px;margin:-2px 0 4px 2px}
.content blockquote{font-size:13.5px;line-height:17px;margin-top:6px}
.signature{left:409px;top:753px;font-size:10px;color:#777;line-height:13px}

.tabs{left:23px;top:787px;width:487px;height:21px;background:linear-gradient(#f4f4f4,#d8d8d8);border-radius:3px;font-size:9.5px;color:#333}
.tabs span{position:absolute;top:5px}
.tabs .on{left:93px;top:-3px;height:24px;width:72px;padding:8px 9px;background:#d0d0d0;border-radius:4px 4px 0 0}
.dropdown{left:118px;top:808px;width:199px;height:77px;background:#cfcfcf;font-size:8.6px;padding-top:2px}
.dropdown div{padding:2px 7px;height:18px}
.dropdown div:first-child{background:#ececec}
.region-select{left:397px;top:815px;width:111px;height:20px;border:1px solid #bbb;border-radius:4px;background:linear-gradient(#fff,#e4e4e4);font-size:10px;padding:4px 10px}
.region-select svg{position:absolute;right:8px;top:6px}
.world-map{left:20px;top:845px;width:400px;height:220px;border-radius:40px;background:radial-gradient(ellipse at 40% 40%,var(--map),#8cc8f7 60%,var(--white) 80%)}

.login{left:520px;width:205px;height:98px;border-radius:5px;padding:6px 10px}
.login.free{top:414px;background:linear-gradient(var(--blue-light),var(--blue))}
.login.paid{top:541px;background:linear-gradient(var(--orange-light),var(--orange))}
.login h3{font-weight:400;color:var(--white);font-size:17px;margin-bottom:7px}
.login .field{height:17px;background:var(--white);border-radius:8px;font-size:8.5px;color:#666;padding:3px 11px;margin-bottom:6px}
.login .btn{position:absolute;left:66px;bottom:-6px;width:77px;height:19px;background:linear-gradient(#fff,#ddd);border-radius:7px;text-align:center;font-size:12px;line-height:19px}
.login-note{font-size:8.5px;right:28px}

.language{left:520px;top:668px;width:205px;height:53px;border:1px solid #ccc;border-radius:4px;background:#f3f3f3;padding:6px 7px;font-size:9.5px}
.language .select{height:18px;background:var(--white);border-radius:3px;color:#888;padding:4px 8px;margin-bottom:4px;position:relative}
.language .select svg{position:absolute;right:6px;top:6px}
.language b{font-size:12px;color:#555;font-family:"EB Garamond",Georgia,serif;font-weight:500}

.passings{left:520px;top:732px;width:205px;height:340px;background:var(--panel);border:1px solid #ccc;border-radius:4px}
.passings h3{position:absolute;left:30px;top:-3px;width:145px;height:25px;background:linear-gradient(#eee,#d4d4d4);border-radius:3px;font-family:"EB Garamond",Georgia,serif;font-weight:400;font-size:16px;text-align:center;line-height:25px;color:#444}
.entry{position:absolute;left:9px;width:186px;height:98px;border-bottom:1px solid var(--line)}
.entry h4{font-family:"EB Garamond",Georgia,serif;font-weight:400;font-size:13px}
.entry p{width:92px;font-size:8.5px;line-height:13px;color:#444;margin-top:3px}
.entry .thumb{position:absolute;right:9px;top:6px;width:82px;height:66px;border:1px solid #bbb}
.entry .tag{position:absolute;right:9px;top:78px;font-size:8.5px}

.partners{left:0;top:1078px;width:750px;height:57px;background:linear-gradient(#f0f0f0,#e0e0e0)}
.partners .badge{position:absolute;top:16px;height:24px;background:#444}
.footer-nav{left:0;top:1137px;width:750px;height:30px;background:linear-gradient(#fff,#ececec);font-family:"EB Garamond",Georgia,serif;font-size:13.5px;color:#555}
.footer-nav ul{list-style:none;display:flex;position:absolute;left:112px;top:6px}
.footer-nav li{padding:0 11px}
.copyright{left:15px;top:1180px;font-size:8px;color:#888}
.social{top:1175px;width:16px;height:16px;border-radius:3px}
</style>
</head>
<body>

<nav class="abs region-bar" aria-label="Regions">
  <ul><li>Australia/NZ</li><li>Canada</li><li>United States</li><li>Israel</li><li>Europe</li><li>UK</li><li>Asia</li><li>Central and South America</li><li>Africa</li></ul>
</nav>

<div class="abs brand"><span class="brand-dot"></span><span class="brand-name">Lanternmerow.net</span></div>

<div class="abs search">Search
  <svg width="14" height="14" viewBox="0 0 14 14"><circle cx="6" cy="6" r="4.2" fill="none" stroke="#666" stroke-width="1.6"/><line x1="9" y1="9" x2="13" y2="13" stroke="#666" stroke-width="2"/></svg>
</div>

<nav class="abs main-nav" style="top:92px">
  <ul><li class="active">Home</li><li>Our mission</li><li>About Us</li><li>Personal Media</li><li>Contact Us</li><li>On-line Forum</li></ul>
</nav>

<div class="abs hero" role="img" aria-label="Photo of a golden Star of David resting on a page of Hebrew text"></div>
<div class="abs hero-arrow" style="left:20px"><svg width="10" height="12"><polygon points="9,0 9,12 1,6" fill="#fff"/></svg></div>
<div class="abs hero-arrow" style="left:700px"><svg width="10" height="12"><polygon points="1,0 1,12 9,6" fill="#fff"/></svg></div>
<div class="abs hero-caption">Welcome to the global Chevra Kadisha network</div>

<div class="abs page-tab">Home</div>

<section class="abs content">
  <h2>Please choose your region</h2>
  <p>Our site has been created for family members to honor their loved ones and to assist the holy work of chevra kadisha members who selflessly prepare a Jewish body and soul for the next stage in it's journey.</p>
  <p>Lanternmerow.net is the global Jewish community's sacred burial society's website and resource portal, for data collation of personal memorial media (obituaries, condolence comments, photos, documents &amp; video), relating to Jewish persons who have passed on.</p>
  <h2 style="margin-top:4px">Our Mission</h2>
  <p class="byline">Eliezer Brandt - Co-founder Lanternmerow.net</p>
  <p>Our mission is to reach out and inform all Jewish people about the chesed v'emes (truth and kindness) of the Chevra Kadisha society and to provide simple and meaningful information, about the life-cycle of a Jewish neshama, using the rich tapestry of sources from our 3000 year tradition.</p>
  <p>Our children – the guarantors to the survival of the Jewish people, can contribute in their own way, by providing and adding content notes to their relatives' media listings, for an eternal memory.</p>
  <p>May we all merit the coming of Moshiach Now, speedily in our days, with the fulfillment of the prophecy.</p>
  <blockquote>“He will swallow up death forever; G-d, the L-ord, will wipe away tears from all faces.”<br>[Yeshayahu 25:8]</blockquote>
</section>
<div class="abs signature">Eliezer Brandt<br>Co-Founder</div>

<div class="abs tabs">
  <span style="left:22px">Local Info</span>
  <span class="on">Soul Search</span>
  <span style="left:193px">Jewish Death &amp; Mourning Customs</span>
</div>
<div class="abs dropdown">
  <div>Chevra Kadisha Funerals (within 7 days)</div>
  <div>Cemetaries Recently Deceased (up to 12mth)</div>
  <div>Stonemasons Soul Search (after 1 year)</div>
  <div>Jewish Media Partners</div>
</div>
<div class="abs region-select">Australia/NZ
  <svg width="9" height="6"><polygon points="0,0 9,0 4.5,6" fill="#333"/></svg>
</div>
<div class="abs world-map" role="img" aria-label="Blue world map for choosing a region"></div>

<form class="abs login free">
  <h3>Free listing</h3>
  <div class="field">Username</div>
  <div class="field">Password</div>
  <div class="btn">Sign in</div>
</form>
<div class="abs login-note" style="top:521px">normal upload</div>

<form class="abs login paid">
  <h3>Paid listings</h3>
  <div class="field">Username</div>
  <div class="field">Password</div>
  <div class="btn">Sign in</div>
</form>
<div class="abs login-note" style="top:650px">multimedia upload like video / audio etc...</div>

<div class="abs language">
  <div class="select">Select Language<svg width="9" height="6"><polygon points="0,0 9,0 4.5,6" fill="#aaa"/></svg></div>
  Powered by <b>Lingo</b> Translate
</div>

<aside class="abs passings">
  <h3>Recent Passings</h3>
  <div class="entry" style="top:30px">
    <h4>Benjamin Farber</h4>
    <p>Lorem Ipsum is simply dummy text of the printing and typesetting industry.</p>
    <div class="thumb" role="img" aria-label="Family photo of the deceased" style="background:linear-gradient(#d9c5b3,#b89a86)"></div>
    <span class="tag">Recently Deceased</span>
  </div>
  <div class="entry" style="top:128px">
    <h4>Benjamin Farber</h4>
    <p>Lorem Ipsum is simply dummy text of the printing and typesetting industry.</p>
    <div class="thumb" role="img" aria-label="Photo of footprints in the sand" style="background:linear-gradient(#c6a077,#9c7650)"></div>
    <span class="tag">Recently Deceased</span>
  </div>
  <div class="entry" style="top:226px;border-bottom:none">
    <h4>Benjamin Farber</h4>
    <p>Lorem Ipsum is simply dummy text of the printing and typesetting industry.</p>
    <div class="thumb" role="img" aria-label="Placeholder listing image" style="background:radial-gradient(#f4a04a,#fff 70%)"></div>
    <span class="tag">Recently Deceased</span>
  </div>
</aside>

<div class="abs partners" aria-label="Jewish media partners">
  <span class="badge" style="left:52px;width:32px"></span>
  <span class="badge" style="left:115px;width:104px"></span>
  <span class="badge" style="left:242px;width:138px;background:#2a4b8d"></span>
  <span class="badge" style="left:400px;width:110px"></span>
  <span class="badge" style="left:537px;width:137px"></span>
</div>

<nav class="abs footer-nav">
  <ul><li>Home</li><li>Our mission</li><li>About Us</li><li>Personal Media</li><li>Contact Us</li><li>On-line Forum</li></ul>
</nav>

<div class="abs copyright">Copyright © 2011. www.lanternmerow.com</div>
<span class="abs social" style="left:606px;background:#3b5998"></span>
<span class="abs social" style="left:629px;background:#33b5e5"></span>
<span class="abs social" style="left:652px;background:#f07b1c"></span>
<span class="abs social" style="left:676px;background:#1f6ca8"></span>
<span class="abs social" style="left:700px;background:#3f7fbf"></span>
<span class="abs social" style="left:725px;top:1172px;width:20px;height:20px;border-radius:50%;background:#333"></span>

</body>
</html>
```